Brochure for a civil enineering company in A4 format

I need a brochure design for our company TIRO Engineering S.r.l.. We are an engineering consultant company. Our main clients are from the infrastructure industry (geotechnical and underground sectors mainly).
We are looking for a 2 pages (4 faces) fold out design with a glued pocket where we can put individual data sheets.
I need A4 format pages.

Target Market(s)

We are an engineering consultant company. Our main clients are from the infrastructure industry (geotechnical and underground sectors mainly).

Industry/Entity Type

Civil Engineer

Font styles to use
Sans Serif

Requirements
Must have
• Overall: 2 pages in A4 format
Essential style. Bright and modern appearance.
Glued pocket
Logo integrated in a picture on the pocket where I would like to insert a slogan (… tiro engineering … reliable solutions …)
Attached are selected images which the designer can use and edit at their own discretion.
Some advice in the following (anyway designers are free to provide their solutions):
Outer sheets:
Front page with name, logo. It could be nice to have the “m” of the logo integrated in a pictures, also a modified picture (I mean modify one of the attached pictures) so to create a general image and do not tie the cover to a specific job.
Back page: offices address and contact email address. Nice to have one space for a slogan.
Inner sheet: text that I upload in the file “inside-sheets”, possibly with pictures on each sheet. In the right faces insert the glued pocket. On this pages insert the section OUR EXPERIENCE ….with a space for a picture of our team.
Nice to have
• Clean and essential design.
Pictures choosing from the atteched ones. Pictures could be modified in a very light manner to make them a general idea of the work ( I mean geotechnical world) without to be immediately linked to a specific site.
Should not have
• excessive frills

```html
<!DOCTYPE html>
<html lang="en">
<head>
<meta charset="utf-8">
<title>TIRO Engineering — Brochure Cover</title>
<link rel="stylesheet" href="https://fonts.googleapis.com/css2?family=Montserrat:wght@400;600;700;800;900&display=swap">
<style>
  :root {
    --paper: #ffffff;
    --ink: #1a1a1a;
    --brand-red: #d7141a;
    --band-grey: #c9c9c9;
    --photo-sky: #8fb4d6;
    --photo-earth: #9b8a6c;
    --photo-green: #7e8d5a;
    --tunnel-dark: #4a4540;
    --tunnel-light: #a79d8d;
  }
  * { margin: 0; padding: 0; box-sizing: border-box; }
  html, body {
    width: 900px; height: 1200px; overflow: hidden;
    background: var(--paper);
    font-family: "Montserrat", sans-serif;
    color: var(--ink);
  }
  .cover { position: relative; width: 900px; height: 1200px; background: var(--paper); }
  .cover-art { position: absolute; inset: 0; }

  .brand { position: absolute; left: 70px; top: 70px; }
  .brand-name {
    font-size: 120px; font-weight: 800; letter-spacing: -3px; line-height: 1;
    color: var(--ink);
  }
  .brand-tagline {
    margin-top: 10px; font-size: 13px; font-weight: 600; letter-spacing: 3px;
    text-transform: uppercase; color: var(--ink);
  }

  .slogan {
    position: absolute; right: 70px; top: 760px; text-align: right;
    font-size: 56px; line-height: 1.08; letter-spacing: -1px;
  }
  .slogan .light { font-weight: 400; }
  .slogan .strong { font-weight: 800; }
  .slogan .accent { color: var(--brand-red); }

  .footer-band {
    position: absolute; left: 0; right: 0; top: 1040px; height: 56px;
    background: var(--ink); display: flex; align-items: center; justify-content: flex-end;
    padding-right: 70px;
  }
  .footer-band .web {
    color: var(--paper); font-size: 22px; font-weight: 600; letter-spacing: 4px;
  }
  .footer-rule {
    position: absolute; left: 0; right: 0; top: 1104px; height: 10px; background: var(--brand-red);
  }
</style>
</head>
<body>
<main class="cover">
  <svg class="cover-art" width="900" height="1200" viewBox="0 0 900 1200">
    <defs>
      <linearGradient id="siteGradient" x1="0" y1="0" x2="0.3" y2="1">
        <stop offset="0" stop-color="var(--photo-sky)"/>
        <stop offset="0.35" stop-color="var(--photo-green)"/>
        <stop offset="1" stop-color="var(--photo-earth)"/>
      </linearGradient>
      <radialGradient id="tunnelGradient" cx="0.5" cy="0.45" r="0.6">
        <stop offset="0" stop-color="var(--tunnel-light)"/>
        <stop offset="1" stop-color="var(--tunnel-dark)"/>
      </radialGradient>
    </defs>

    <path class="site-photo" role="img" aria-label="Photograph of a coastal hillside construction site with earthworks and slope stabilisation"
          d="M400 0 H900 V560 C720 575 540 620 340 700 C345 480 370 240 400 0 Z"
          fill="url(#siteGradient)"/>

    <path class="swoosh-grey" d="M0 720 C300 640 600 580 900 555 L900 575 C600 600 300 665 0 745 Z" fill="var(--band-grey)"/>
    <path class="swoosh-black" d="M0 752 C300 672 600 610 900 585 L900 595 C600 620 300 685 0 765 Z" fill="var(--ink)"/>
    <path class="swoosh-red" d="M0 775 C300 695 600 630 900 605 L900 640 C600 662 300 725 0 810 Z" fill="var(--brand-red)"/>

    <circle class="inset-ring" cx="230" cy="830" r="168" fill="var(--paper)" stroke="var(--brand-red)" stroke-width="8"/>
    <circle class="inset-photo" role="img" aria-label="Photograph of a tunnel under construction with drilling equipment"
            cx="230" cy="830" r="150" fill="url(#tunnelGradient)"/>
  </svg>

  <header class="brand">
    <div class="brand-name">tiro</div>
    <div class="brand-tagline">tiro engineering · reliable solutions</div>
  </header>

  <h1 class="slogan">
    <span class="light accent">We</span> <span class="light">work to</span><br>
    <span class="strong">mitigate risk</span> <span class="light accent">and</span><br>
    <span class="strong">reduce</span> <span class="strong accent">uncertainty</span>
  </h1>

  <footer class="footer-band"><span class="web">www.tiroengineering.org</span></footer>
  <div class="footer-rule"></div>
</main>
</body>
</html>
```